real esate business card with company logo and name

we need a business card design for a real esate company

The company name is Walsh & Brand Pty Ltd, and we have our logo designed and will upload. We want classic or moden feel. Black or white background. looks more textured. Should include folowinginformations
Owen Walsh and Lucy Brand
Sales Agents & Onsite Manager
p: 07 5948 2063
F: 07 5948 2174
M:0431 857 219
3/42 Marlow Crescent, FERNLEA QLD 4213

We want this business card looks professonal. Thank you in advance.

Industry/Entity Type

Real Estate Agent

Contact Information for Business Card

Owen Walsh and Lucy Brand
Onsite Manager & Sales Agents
p: 07 5948 2063
M:0431 857 219

Font styles to use
Serif

Colors
000000
fbfbfb
333333
959595

Requirements
Must have
• company logo and name, black or white back ground

```html
<!DOCTYPE html>
<html lang="en">
<head>
<meta charset="utf-8">
<title>Walsh &amp; Brand Pty Ltd — Business Card</title>
<link href="https://fonts.googleapis.com/css2?family=Roboto+Condensed:wght@400;500&family=Open+Sans:wght@400;500&display=swap" rel="stylesheet">
<style>
  :root {
    --backdrop: #a6a3a4;
    --card: #fbfbfb;
    --ink: #4a4a4d;
    --ink-soft: #8a8a8d;
    --band-dark: #5a5a5e;
    --band-light: #b9b9bb;
    --rule: #e2e2e2;
    --icon: #a9a9ab;
  }
  * { box-sizing: border-box; margin: 0; padding: 0; }
  html, body { width: 1200px; height: 1200px; overflow: hidden; }
  body {
    background: var(--backdrop);
    position: relative;
    font-family: "Open Sans", sans-serif;
    color: var(--ink);
  }
  .card {
    position: absolute;
    left: 242px;
    width: 710px;
    height: 410px;
    background: var(--card);
    border-radius: 24px;
    overflow: hidden;
  }
  .card--front { top: 120px; }
  .card--back { top: 646px; }

  .brand {
    position: absolute;
    display: flex;
    flex-direction: column;
    align-items: center;
    gap: 26px;
  }
  .brand__square {
    width: 120px;
    height: 120px;
    background: var(--band-dark);
  }
  .brand__name {
    font-family: "Roboto Condensed", sans-serif;
    font-weight: 400;
    font-size: 23px;
    letter-spacing: 0.5px;
    color: var(--ink-soft);
    text-transform: uppercase;
    white-space: nowrap;
  }
  .card--front .brand { left: 0; right: 0; top: 112px; }
  .card--back .brand { left: 0; width: 352px; top: 88px; }

  .divider {
    position: absolute;
    left: 352px;
    top: 42px;
    width: 1px;
    height: 270px;
    background: var(--rule);
  }
  .contact {
    position: absolute;
    left: 384px;
    top: 106px;
  }
  .contact__names {
    font-family: "Roboto Condensed", sans-serif;
    font-weight: 400;
    font-size: 26px;
    color: var(--ink);
    white-space: nowrap;
  }
  .contact__role {
    font-family: "Roboto Condensed", sans-serif;
    font-size: 14px;
    color: var(--ink);
    margin-top: 8px;
  }
  .contact__list {
    list-style: none;
    margin-top: 20px;
  }
  .contact__item {
    display: flex;
    align-items: center;
    gap: 18px;
    height: 27px;
    font-size: 16px;
    color: var(--ink);
    letter-spacing: 0.3px;
  }
  .contact__icon { width: 16px; height: 16px; fill: var(--icon); flex: none; }

  .band {
    position: absolute;
    left: 0;
    right: 0;
    bottom: 0;
    height: 60px;
  }
  .band svg { display: block; }
  .band__address {
    position: absolute;
    right: 30px;
    top: 16px;
    font-family: "Roboto Condensed", sans-serif;
    font-weight: 500;
    font-size: 16px;
    color: var(--ink);
    white-space: nowrap;
  }
</style>
</head>
<body>

  <section class="card card--front" aria-label="Card front">
    <div class="brand">
      <div class="brand__square"></div>
      <div class="brand__name">Walsh &amp; Brand Pty Ltd.</div>
    </div>
  </section>

  <section class="card card--back" aria-label="Card back">
    <div class="brand">
      <div class="brand__square"></div>
      <div class="brand__name">Walsh &amp; Brand Pty Ltd.</div>
    </div>

    <div class="divider"></div>

    <div class="contact">
      <p class="contact__names">Owen Walsh &amp; Lucy Brand</p>
      <p class="contact__role">Sales Agents &amp; Onsite Manager</p>
      <ul class="contact__list">
        <li class="contact__item">
          <svg class="contact__icon" viewBox="0 0 16 16" aria-hidden="true"><rect x="4" y="1" width="8" height="14" rx="1.5"/><rect x="5.3" y="3" width="5.4" height="9" fill="#fbfbfb"/></svg>
          0431 857 219
        </li>
        <li class="contact__item">
          <svg class="contact__icon" viewBox="0 0 16 16" aria-hidden="true"><path d="M1 6c0-2 3-3 7-3s7 1 7 3v1h-4V5.5H5V7H1z"/><path d="M4 8h8l2 6H2z"/></svg>
          07 5948 2063
        </li>
        <li class="contact__item">
          <svg class="contact__icon" viewBox="0 0 16 16" aria-hidden="true"><rect x="4" y="1" width="8" height="4"/><rect x="1" y="6" width="14" height="6" rx="1"/><rect x="4" y="10" width="8" height="5"/></svg>
          07 5948 2174
        </li>
      </ul>
    </div>

    <div class="band">
      <svg width="710" height="60" viewBox="0 0 710 60" aria-hidden="true">
        <rect x="0" y="30" width="710" height="30" fill="var(--band-dark)"/>
        <polygon points="326,0 710,0 710,60 306,60" fill="var(--band-light)"/>
      </svg>
      <p class="band__address">3/42 Marlow Crescent, FERNLEA QLD 4213</p>
    </div>
  </section>

</body>
</html>
```